Heron Loan Partners Business Card

We need a business card design for our mortgage servicing company. In addition to servicing the loans of homeowners, we help homeowners with purchasing their homes and any mortgage refinancing. We would like to see designs that use the colors in the logo attached below (gold-ish yellow and navy blue), and any other design you deem fit! The design should communicate a simpler life with smart mortgages provided by Heron.

```html
<!DOCTYPE html>
<html lang="en">
<head>
<meta charset="utf-8">
<title>Heron Loan Partners Business Card</title>
<link href="https://fonts.googleapis.com/css2?family=Poppins:wght@400;500;600&family=Raleway:wght@500;600&display=swap" rel="stylesheet">
<style>
  :root {
    --navy: #262052;
    --gold: #e0b13e;
    --white: #ffffff;
    --backdrop: #b3b3b3;
  }
  * { margin: 0; padding: 0; box-sizing: border-box; }
  html, body { width: 1093px; height: 1200px; overflow: hidden; }
  body {
    background: var(--backdrop);
    font-family: "Poppins", sans-serif;
    position: relative;
  }
  .card {
    position: absolute;
    left: 265px;
    width: 578px;
    height: 357px;
    border-radius: 26px;
    overflow: hidden;
  }
  .card--front { top: 226px; background: var(--navy); }
  .card--back { top: 621px; background: var(--navy); }

  .front-top {
    position: absolute; left: 0; top: 0; width: 100%; height: 189px;
    background: var(--white);
    border-bottom: 3px solid var(--gold);
  }
  .wordmark {
    position: absolute; left: 0; width: 100%;
    text-align: center;
    font-family: "Poppins", sans-serif;
    font-weight: 600;
    font-size: 44px;
    letter-spacing: 1px;
  }
  .front-top .wordmark { top: 66px; color: var(--navy); }
  .card--back .wordmark { top: 150px; color: var(--gold); }

  .person {
    position: absolute; right: 345px; top: 219px;
    text-align: right;
  }
  .person-name {
    font-family: "Raleway", sans-serif;
    font-weight: 600; font-size: 24px; line-height: 28px;
    color: var(--gold);
  }
  .person-title {
    font-size: 16px; line-height: 20px; color: var(--white);
  }
  .divider {
    position: absolute; left: 288px; top: 220px;
    width: 2px; height: 57px; background: var(--white);
  }
  .contacts {
    position: absolute; left: 308px; top: 216px;
    list-style: none;
  }
  .contacts li {
    display: flex; align-items: center; gap: 7px;
    height: 21px;
    font-size: 17px; color: var(--white);
  }
  .contacts svg { width: 15px; height: 15px; flex: none; }
  .address {
    position: absolute; left: 0; width: 100%; top: 306px;
    text-align: center;
    font-size: 16.5px; color: var(--white);
  }
</style>
</head>
<body>
  <section class="card card--front">
    <div class="front-top">
      <div class="wordmark">Heron Mortgage</div>
    </div>
    <div class="person">
      <div class="person-name">Daniel Harper</div>
      <div class="person-title">Managing Director</div>
    </div>
    <div class="divider"></div>
    <ul class="contacts">
      <li>
        <svg viewBox="0 0 16 16" aria-hidden="true"><path fill="var(--gold)" d="M4 1.5l2 3-1.3 1.3c.8 1.9 2.1 3.3 4 4.2L10 8.7l3 2-1 2.6c-.3.6-1 .9-1.6.7C6 12.7 3.3 10 2 5.6c-.2-.6.1-1.3.7-1.6z"/><path fill="none" stroke="var(--gold)" stroke-width="1.3" d="M10 2.5a4 4 0 0 1 3.5 3.5M9.6 4.8a2 2 0 0 1 1.6 1.6"/></svg>
        044-555 018 274
      </li>
      <li>
        <svg viewBox="0 0 16 16" aria-hidden="true"><rect x="1" y="3.5" width="14" height="9.5" fill="var(--gold)"/><path d="M1 3.5l7 5.5 7-5.5M1 13l5-4.5M15 13l-5-4.5" fill="none" stroke="var(--navy)" stroke-width="1.1"/></svg>
        hello@heronloans.com
      </li>
      <li>
        <svg viewBox="0 0 16 16" aria-hidden="true"><g fill="none" stroke="var(--gold)" stroke-width="1.3"><circle cx="8" cy="8" r="6.5"/><ellipse cx="8" cy="8" rx="3" ry="6.5"/><path d="M1.5 8h13M2.5 4.8h11M2.5 11.2h11"/></g></svg>
        www.heronloans.com
      </li>
    </ul>
    <p class="address">87 Harbor Crest Road 30418, Country Name</p>
  </section>

  <section class="card card--back">
    <div class="wordmark">Heron Mortgage</div>
  </section>
</body>
</html>
```